Kelvaro.ch is looking for business card letterhead and envelope C5 with WOW effect

We need a strong business card for our company Kelvaro.ch, logo is available. You want a black or dark background on which the logo Stark r% 26 # 252; appears. Letterhead and envelope in C5 format should be in a similar design, but does not have to be We need a strong business card for our company Kelvaro.ch, logo is available. A black or dark background is desired, on which the logo Stark comes across. The letterhead and the envelope in C5 format should have a similar design.

Target Market(s)

Private customers as well as entrepreneurs

Contact Information for Business Card

E-mail: info@kelvaro-example.ch
Web.www.Kelvaro-example.ch
Tel: +41 ( 0 ) 79 482 6037
Adresse:
Lindenweg 14
9406 Tarnbach

Hier kann man Icons verwenden für Email,Tel und Adressse

Font styles to use
Other font styles liked:
• Dubai,bold

Colors

Designer to choose colors to be used in the design.

Requirements
Must have
• WOW effect
Nice to have
• R% 26 # 252; back business card with our service listings. - VEHICLE LABELING - SHOP WINDOW LABELING - STICKERS AND MUCH MORE ... in red color

```html
<!DOCTYPE html>
<html lang="en">
<head>
<meta charset="utf-8">
<title>Kelvaro.ch – Letterhead and C5 Envelope</title>
<link href="https://fonts.googleapis.com/css2?family=Open+Sans:wght@400;600;700&display=swap" rel="stylesheet">
<style>
  :root {
    --bg: #e6e6e6;
    --paper: #ffffff;
    --ink: #1a1a1a;
    --text: #444444;
    --muted: #555555;
    --brand-yellow: #f5c116;
    --brand-black: #0c0c0c;
    --rule: #8a8a8a;
    --signature: #b9b9b9;
  }
  * { box-sizing: border-box; margin: 0; padding: 0; }
  html, body { width: 1200px; height: 1200px; overflow: hidden; }
  body {
    background: var(--bg);
    font-family: "Open Sans", Arial, sans-serif;
    color: var(--text);
    position: relative;
  }

  /* Brand wordmark */
  .wordmark { display: flex; align-items: center; gap: 10px; }
  .wordmark__dot { width: 22px; height: 22px; border-radius: 50%; background: var(--brand-yellow); }
  .wordmark__name { font-weight: 700; color: var(--ink); letter-spacing: 0.5px; }

  /* Letterhead */
  .letterhead {
    position: absolute; left: 80px; top: 230px;
    width: 556px; height: 714px;
    background: var(--paper);
    box-shadow: 0 4px 14px rgba(0,0,0,0.18);
  }
  .letterhead .wordmark { position: absolute; left: 0; right: 0; top: 34px; justify-content: center; }
  .letterhead .wordmark__name { font-size: 17px; }
  .letter {
    position: absolute; left: 52px; right: 54px; top: 128px;
    font-size: 9px; line-height: 11px;
  }
  .letter__date { margin-bottom: 10px; }
  .letter__recipient { margin-bottom: 30px; }
  .letter__salutation { margin-bottom: 17px; }
  .letter__body p { line-height: 16px; margin-bottom: 16px; text-align: justify; }
  .letter__closing { margin-top: 26px; }
  .letter__signature { width: 130px; height: 16px; margin: 8px 0 8px; background: var(--signature); opacity: 0.5; border-radius: 8px; }
  .letter__signer { font-size: 11.5px; color: var(--ink); line-height: 15px; }
  .letter__role { margin-top: 4px; }

  .letterhead__footer {
    position: absolute; left: 0; right: 0; bottom: 0;
    text-align: center; color: var(--ink);
  }
  .letterhead__address { font-size: 10.5px; padding-bottom: 4px; }
  .letterhead__rule { width: 348px; height: 1px; background: var(--rule); margin: 0 auto 6px; }
  .letterhead__contact { font-size: 10.5px; padding-bottom: 6px; }
  .label, .web { color: var(--brand-yellow); }

  .stripe { display: flex; height: 10px; }
  .stripe__yellow { background: var(--brand-yellow); }
  .stripe__black { background: var(--brand-black); flex: 1; }
  .letterhead .stripe__yellow { width: 274px; }

  /* Envelope front */
  .envelope {
    position: absolute; left: 716px; width: 430px; height: 216px;
    background: var(--paper);
    box-shadow: 0 4px 14px rgba(0,0,0,0.18);
  }
  .envelope--front { top: 492px; }
  .envelope--front .wordmark { position: absolute; left: 26px; top: 20px; gap: 8px; }
  .envelope--front .wordmark__dot { width: 18px; height: 18px; }
  .envelope--front .wordmark__name { font-size: 12px; }
  .envelope__address { position: absolute; left: 33px; bottom: 19px; font-size: 8px; color: var(--ink); }
  .envelope--front .stripe { position: absolute; left: 0; right: 0; bottom: 0; height: 7px; }
  .envelope--front .stripe__yellow { width: 221px; }

  /* Envelope back */
  .envelope--back { top: 743px; left: 717px; width: 429px; height: 213px; }
  .envelope__flap { position: absolute; left: 0; top: 0; width: 429px; height: 51px; }
  .envelope__flap-name {
    position: absolute; left: 0; right: 0; top: 17px;
    text-align: center; font-size: 11px; font-weight: 700;
    color: var(--brand-yellow); letter-spacing: 0.5px;
  }
</style>
</head>
<body>

  <section class="letterhead">
    <div class="wordmark">
      <span class="wordmark__dot"></span>
      <span class="wordmark__name">KELVARO.CH</span>
    </div>

    <div class="letter">
      <p class="letter__date">Issuing Date: May 5, 2018</p>
      <p class="letter__recipient">Name Of Employee Mr. XYZABC<br>Address of Employee<br>Address Line 2 etc..</p>
      <p class="letter__salutation">Dear Mr.XYZABC</p>
      <div class="letter__body">
        <p>Lorem Ipsum has been the industry's standard dummy text ever since the 1500s, when an unknown printer took a galley of type and scrambled it to make a type specimen book. It has survived not only five centuries, but also the leap into electronic typesetting, remaining essentially unchanged. It was popularised in the 1960s with the release of Letraset sheets containing Lorem Ipsum passages, and more recently with desktop publishing software like Aldus PageMaker including versions of Lorem Ipsum.</p>
        <p>Lorem Ipsum is simply dummy text of the printing and typesetting industry. Lorem Ipsum has been the industry's standard dummy text ever since the 1500s, when an unknown printer took a galley of type and scrambled it to make a type specimen book.</p>
        <p>It has survived not only five centuries, but also the leap into electronic typesetting, remaining essentially unchanged. It was popularised in the 1960s with the release of Letraset sheets containing Lorem Ipsum passages.</p>
      </div>
      <p class="letter__closing">Yours Sincerely</p>
      <div class="letter__signature" role="img" aria-label="Handwritten signature of Matthias Brenner"></div>
      <p class="letter__signer">Matthias Brenner</p>
      <p class="letter__role">Managing Director</p>
    </div>

    <footer class="letterhead__footer">
      <p class="letterhead__address">Lindenweg 14, 9406 Tarnbach</p>
      <div class="letterhead__rule"></div>
      <p class="letterhead__contact"><span class="label">PHONE:</span> +41 ( 0 ) 79 482 6037 | <span class="label">EMAIL:</span> info@kelvaro-example.ch &nbsp;| &nbsp;<span class="web">www.Kelvaro-example.ch</span></p>
      <div class="stripe"><span class="stripe__yellow"></span><span class="stripe__black"></span></div>
    </footer>
  </section>

  <section class="envelope envelope--front">
    <div class="wordmark">
      <span class="wordmark__dot"></span>
      <span class="wordmark__name">KELVARO.CH</span>
    </div>
    <p class="envelope__address">Lindenweg 14,9406 Tarnbach</p>
    <div class="stripe"><span class="stripe__yellow"></span><span class="stripe__black"></span></div>
  </section>

  <section class="envelope envelope--back">
    <svg class="envelope__flap" viewBox="0 0 429 51" aria-hidden="true">
      <polygon points="0,0 429,0 413,51 16,51" fill="#0c0c0c"/>
    </svg>
    <p class="envelope__flap-name">KELVARO.CH</p>
  </section>

</body>
</html>
```